KorvaNest - Home Income and Business Resources Platform

I am looking for a website template for a multi-purposed website. This website will feature:

1.) Website Directory with Ratings & comments on listings
2.) Company Blog
3.) Homepage with Content (see files for homepage mock)

I would like the Design to have a default width 1170px (wider then normal)

Of course I am looking for Pages for Listings to be designed.

Great looking BLOG Layout: http://journal.plimworks.example/html/blog.html

I would like 4 Versions of a Website Directory Listing "Box"
1.) Basic Listing Box
2.) Sponsored Listing Box
3.) Recommended Listing Box
4.) Stay Away From Listing Box

Information on the Listing Page (Like on a Category Page)
Site Name, Site URL, Website Image, # of Views, Rating and # of Comments

Information on the Listing Details Page:
Same as ABOVE + About website Description, Vornic Score, Category Information

Decent looking examples is here: https://samples.trevolin.example/directory/computers/ and http://www.zqrankhub.example/.

I will include some sketches and screenshots of things I like/looking for. As designers,you have creative freedom and are encouraged to show this. This is Phase one of this project and winning designer is guaranteed to have future work for this project.

Target Market(s)

Directory, business, websites

Industry/Entity Type

Business

Coding

Coded - Design and coding required

Number of Pages Required

5+ page

Font styles to use
Sans Serif

Colors

Designer to choose colors to be used in the design.

Requirements
Must have
• Professional yet clean look. The use of Icons & images
• Unique Look
Should not have
• Any exact copies of any examples I provided

```html
<!DOCTYPE html>
<html lang="en">
<head>
<meta charset="utf-8">
<title>KorvaNest</title>
<link href="https://fonts.googleapis.com/css2?family=Lato:wght@400;700&display=swap" rel="stylesheet">
<style>
  :root {
    --brand: #1e88d6;
    --brand-dark: #1565b8;
    --text: #555;
    --heading: #222;
    --border: #e3e3e3;
    --bg: #ffffff;
  }
  * { box-sizing: border-box; margin: 0; padding: 0; }
  html, body { width: 1200px; height: 902px; overflow: hidden; background: var(--bg); }
  body { font-family: 'Lato', sans-serif; color: var(--text); position: relative; border-top: 2px solid var(--brand); }

  .site-logo { position: absolute; left: 100px; top: 22px; font-size: 30px; font-weight: 700; color: var(--brand); }
  .menu-toggle { position: absolute; right: 99px; top: 30px; display: flex; align-items: center; gap: 10px; font-size: 16px; font-weight: 700; color: var(--heading); }
  .menu-toggle svg { display: block; }

  .hero { position: absolute; left: 99px; top: 81px; width: 769px; height: 297px;
    background: linear-gradient(110deg, #8a7563 0%, #3f4f66 45%, #2b3140 70%, #7f8da0 100%); }
  .hero-text { position: absolute; left: 290px; top: 176px; color: #fff; text-shadow: 0 1px 3px rgba(0,0,0,.5); }
  .hero-title { font-size: 39px; font-weight: 700; margin-bottom: 8px; }
  .hero-lead { font-size: 20px; line-height: 30px; width: 470px; }

  .card { position: absolute; top: 399px; width: 248px; height: 385px; background: #fff;
    box-shadow: 0 0 4px rgba(0,0,0,.14); }
  .card-media { height: 192px; }
  .card-body { padding: 20px 10px 0 18px; }
  .card-title { font-size: 15.4px; font-weight: 400; color: var(--brand); line-height: 24px; margin-bottom: 6px; white-space: nowrap; }
  .card-text { font-size: 12.6px; line-height: 24px; color: #666; padding-right: 6px; }
  .card-link { display: inline-block; margin-top: 6px; font-size: 12.6px; line-height: 18px; color: var(--brand); text-decoration: underline; }

  .sidebar-panel { position: absolute; left: 886px; top: 83px; width: 215px; height: 470px; background: #fff;
    box-shadow: 0 0 4px rgba(0,0,0,.14); }
  .panel-head { height: 53px; background: linear-gradient(180deg, #2a8fe0, #1a6fc4); color: #fff;
    font-size: 22px; padding: 12px 23px; }
  .sponsor { position: absolute; left: 22px; width: 167px; height: 93px; background: #fff;
    box-shadow: 0 0 3px rgba(0,0,0,.16); display: flex; align-items: center; justify-content: center;
    font-size: 15px; font-weight: 700; color: #333; }

  .ad-box { position: absolute; left: 886px; top: 569px; width: 215px; height: 214px;
    box-shadow: 0 0 4px rgba(0,0,0,.14); overflow: hidden; }
  .ad-head { height: 35px; background: linear-gradient(180deg, #2a8fe0, #1a6fc4); color: #fff;
    font-size: 12.5px; font-weight: 700; padding: 10px 8px; display: flex; justify-content: space-between; align-items: center; }
  .ad-media { height: 179px; background: linear-gradient(135deg, #6d8a5a 0%, #c23a3a 45%, #e9e3d6 65%, #b3262e 100%); }
  .ad-close { position: absolute; right: 0; bottom: 0; width: 110px; height: 32px; background: #1e88d6;
    color: #fff; font-size: 12.5px; display: flex; align-items: center; justify-content: space-between; padding: 0 7px; }

  .footer-rule { position: absolute; left: 99px; top: 829px; width: 1002px; border-top: 1px solid #ccc; }
  .copyright { position: absolute; left: 0; width: 1200px; top: 859px; text-align: center; font-size: 13.5px; color: #666; }
</style>
</head>
<body>
  <div class="site-logo">KorvaNest</div>
  <div class="menu-toggle">Menu
    <svg width="19" height="16" viewBox="0 0 19 16"><rect y="0" width="19" height="3.5" fill="#1e88d6"/><rect y="6.2" width="19" height="3.5" fill="#1e88d6"/><rect y="12.4" width="19" height="3.5" fill="#1e88d6"/></svg>
  </div>

  <section class="hero" role="img" aria-label="Photo of business people talking at a meeting table">
    <div class="hero-text">
      <h1 class="hero-title">About KorvaNest</h1>
      <p class="hero-lead">Lorem ipsum dolor sit amet, consectetur adipiscing elit. Morbi egestas arcu vel quam consequat.</p>
    </div>
  </section>

  <article class="card" style="left:99px">
    <div class="card-media" role="img" aria-label="Photo of colleagues reviewing papers together" style="background:linear-gradient(135deg,#a8876b,#d98a4a 50%,#7a6a60)"></div>
    <div class="card-body">
      <h2 class="card-title">Home Income<br>&amp; Business Resources directory</h2>
      <p class="card-text">Find what you need, when you need it.The KorvaNest website directory is your one-stop.</p>
      <a class="card-link" href="#">Read More...</a>
    </div>
  </article>

  <article class="card" style="left:359px">
    <div class="card-media" role="img" aria-label="Photo of a hand signing a document with a pen" style="background:linear-gradient(135deg,#e8e8e6,#cfd2d6 55%,#2c3447)"></div>
    <div class="card-body">
      <h2 class="card-title">Advertising<br>Benefits</h2>
      <p class="card-text">Everyone needs to advertise and we know just how to get your offer out to the right people</p>
      <a class="card-link" href="#">Read More...</a>
    </div>
  </article>

  <article class="card" style="left:620px">
    <div class="card-media" role="img" aria-label="Photo of a hand holding a fan of banknotes over a notebook" style="background:linear-gradient(135deg,#ecebe8,#d7b8a0 50%,#5a5d63)"></div>
    <div class="card-body">
      <h2 class="card-title">Earning With<br>KorvaNest</h2>
      <p class="card-text">Join KorvaNest and start earning money. When you share KorvaNest and lock..</p>
      <a class="card-link" href="#">Read More...</a>
    </div>
  </article>

  <aside class="sidebar-panel">
    <div class="panel-head">Sponsors List</div>
    <div class="sponsor" style="top:62px">Farline Co</div>
    <div class="sponsor" style="top:164px">Tidewell Inn</div>
    <div class="sponsor" style="top:266px">Mervane</div>
    <div class="sponsor" style="top:368px">Quillory</div>
  </aside>

  <aside class="ad-box">
    <div class="ad-head">Add By Someone
      <svg width="11" height="11" viewBox="0 0 11 11"><circle cx="5.5" cy="5.5" r="5.5" fill="#fff"/><rect x="4.7" y="4.5" width="1.6" height="4" fill="#1a6fc4"/><circle cx="5.5" cy="3" r="0.9" fill="#1a6fc4"/></svg>
    </div>
    <div class="ad-media" role="img" aria-label="Advertisement collage of food offers and discounts"></div>
    <div class="ad-close">Close This Ad
      <svg width="9" height="9" viewBox="0 0 9 9"><path d="M1 1L8 8M8 1L1 8" stroke="#fff" stroke-width="2"/></svg>
    </div>
  </aside>

  <div class="footer-rule"></div>
  <p class="copyright">Copyright &copy; 2017 - KorvaNest.Allrights Reserved.</p>
</body>
</html>
```